Meridale Bed Company Needs Business Card

Looking for a very nice looking business card. Creative but not extravagant. We sell beds and pillows across the U.S. and need something professional but catchy. I have attached the logo.

Name : Devin Holt
Title : President
Phone : (800) 471-2960
Email: sleep@quilmora.com
Website: www.quilmora.com

Can be single-sided or double-sided
horizontal or vertical

Can use Blues/Greys

Target Market(s)

Mass Market

Industry/Entity Type

Retail

Contact Information for Business Card

Name : Devin Holt
Title : President
Phone : (800) 471-2960
Email: sleep@quilmora.com
Website: www.quilmora.com

Requirements
Must have
• Clean, Modern, Smooth
• Can use Blues/Greys
• On the other side without the information - have something simple like www.quilmora.com or our logo
Nice to have
• Surprise me
Should not have
• Nothing crazy, nothing cluttered

```html
<!DOCTYPE html>
<html lang="en">
<head>
<meta charset="utf-8">
<title>Quilmora Business Card</title>
<link rel="stylesheet" href="https://fonts.googleapis.com/css2?family=Arimo:wght@400;700&display=swap">
<style>
  :root {
    --stage: #e9ecef;
    --card-white: #ffffff;
    --brand-blue: #2ea3db;
    --brand-blue-light: #4bb6e6;
    --text-grey: #555a5e;
    --pattern-tint: #eef4f8;
    --pattern-tint-2: #f8fafb;
  }
  * { box-sizing: border-box; margin: 0; padding: 0; }
  html, body { width: 1200px; height: 843px; overflow: hidden; }
  body {
    background: var(--stage);
    font-family: "Arimo", Arial, sans-serif;
    position: relative;
  }
  .card {
    position: absolute;
    width: 560px;
    height: 320px;
    background: var(--card-white);
    box-shadow: 0 6px 22px rgba(0,0,0,0.12);
    overflow: hidden;
  }
  .card-back { left: 70px; top: 70px; display: flex; align-items: center; justify-content: center; }
  .brand-name {
    font-family: "Arimo", Arial, sans-serif;
    font-weight: 400;
    font-size: 92px;
    letter-spacing: 2px;
    color: var(--brand-blue);
  }
  .card-front { left: 570px; top: 453px; display: flex; flex-direction: column; }
  .band-top { height: 76px; background: linear-gradient(90deg, var(--brand-blue), var(--brand-blue-light)); }
  .band-bottom { flex: 1; background: linear-gradient(90deg, var(--brand-blue), var(--brand-blue-light)); }
  .info-band {
    height: 146px;
    position: relative;
  }
  .info-pattern {
    position: absolute; inset: 0;
    background: linear-gradient(90deg, var(--pattern-tint), var(--pattern-tint-2) 60%, var(--pattern-tint));
  }
  .contact {
    position: absolute;
    left: 178px; top: 28px;
    color: var(--text-grey);
    font-size: 15px;
    line-height: 1.45;
  }
  .contact-name { font-size: 21px; font-weight: 700; color: var(--brand-blue); }
  .contact-title { font-size: 17px; font-weight: 400; color: var(--text-grey); }
  .label { color: var(--brand-blue); font-weight: 700; }
  .contact-web { letter-spacing: 3px; font-size: 14px; padding-left: 40px; }
</style>
</head>
<body>
  <section class="card card-back" aria-label="Card back">
    <span class="brand-name">quilmora</span>
  </section>

  <section class="card card-front" aria-label="Card front">
    <div class="band-top"></div>
    <div class="info-band">
      <div class="info-pattern" role="img" aria-label="Faint repeating brand wordmark pattern"></div>
      <div class="contact">
        <p><span class="contact-name">Devin Holt -</span> <span class="contact-title">President</span></p>
        <p><span class="label">P:</span> (800) 471-2960 &nbsp;<span class="label">E:</span> sleep@quilmora.com</p>
        <p class="contact-web">www.quilmora.com</p>
      </div>
    </div>
    <div class="band-bottom"></div>
  </section>
</body>
</html>
```